13 Varno - new website design project

Our company Varno Electrical is developing a new lead generation website focused on Electrical, LED Lighting and Solar Power. We need a high converting website.

Example of our current website is www.varnoelectrical-example.com.au You can take content from this website for this new design. Our colours are red, black and white. For our new website we would like to promote Varno, Spark Every Day. Please listen to the jingle.

The below link is the company jingle that we have developed.
http://www.tunecraftdemo.com.au/vrn-tc-v1/

The key for this brief is to generate leads for Electrical, LED Lighting (for commercial) and Solar Power & Storage.

Target Market(s)

Business owners in Melbourne Victoria

Number of Pages Required

4 page

Colors
ec1f27
ffffff

Requirements
Must have
• This page must be clean, be in line with company branding and a high converting lead website.

```html
<!DOCTYPE html>
<html lang="en">
<head>
<meta charset="utf-8">
<title>Varno Electrical</title>
<link href="https://fonts.googleapis.com/css2?family=Roboto:ital,wght@0,300;0,400;0,500;0,700;1,400&display=swap" rel="stylesheet">
<style>
:root{
  --red:#ec1f27;
  --red-soft:#f0686c;
  --red-deep:#c8141b;
  --ink:#1d1d1d;
  --text:#444;
  --grey-bg:#f2f3f5;
  --white:#fff;
  --line:#e9787c;
}
*{box-sizing:border-box;margin:0;padding:0}
html,body{width:1200px;height:2317px;overflow:hidden}
body{font-family:'Roboto',Arial,sans-serif;color:var(--text);background:var(--white);position:relative}
.wrap{width:1097px;margin:0 auto;position:relative}
.dotted{border-top:2px dotted var(--line);width:1097px;margin:0 auto}

/* header */
.site-header{height:75px;border-top:4px solid var(--red-deep);background:var(--white);position:relative}
.brand{position:absolute;left:53px;top:14px;display:flex;align-items:center;gap:8px}
.brand-mark{width:26px;height:26px;border-radius:50%;background:var(--red)}
.brand-name{font-size:30px;font-weight:700;color:var(--ink);letter-spacing:1px}
.main-nav{position:absolute;left:374px;top:26px;display:flex;gap:37px;font-size:13px;color:var(--ink)}
.chat{position:absolute;left:980px;top:26px;font-size:13px;color:var(--ink)}
.call-btn{position:absolute;left:1061px;top:17px;background:var(--red-deep);color:#fff;font-size:13px;font-weight:700;padding:7px 10px;border-radius:4px}

/* hero */
.hero{height:488px;background:linear-gradient(160deg,#1d2b55 0%,#2c3e6b 35%,#8a7a5a 60%,#3b4a2a 85%,#2b3420 100%);position:relative}
.hero-title{position:absolute;left:0;right:0;top:148px;text-align:center;color:#fff;font-weight:300;font-size:33px;line-height:39px;letter-spacing:1px}
.hero-title strong{font-weight:700;font-size:40px}

/* welcome */
.welcome{height:110px;text-align:center;padding-top:4px}
.section-title{font-size:22px;font-weight:500;color:var(--ink);text-align:center}
.section-title span{color:var(--red)}
.welcome .dotted{margin-top:10px}
.welcome p{font-size:12.5px;line-height:20px;width:1097px;margin:16px auto 0;color:var(--text)}

/* services */
.services{height:324px;background:var(--grey-bg);padding-top:14px}
.tabs{display:flex;justify-content:center;gap:8px;font-size:17px;font-weight:500;color:var(--ink)}
.tab{padding:10px 18px;border:1px solid transparent;border-radius:3px}
.tab.active{border-color:var(--red);color:var(--red);background:#fff}
.services .dotted{margin-top:14px}
.cards{width:1097px;margin:48px auto 0;display:flex;justify-content:space-between}
.card{width:347px;height:154px;position:relative}
.card-photo{position:absolute;inset:0;border-radius:4px}
.card:nth-child(1) .card-photo{background:linear-gradient(120deg,#8c6b4a,#d9d4cc 55%,#3a5da8)}
.card:nth-child(2) .card-photo{background:linear-gradient(180deg,#c9ced6,#8e97a4 60%,#b7a88f)}
.card:nth-child(3) .card-photo{background:linear-gradient(160deg,#5f86b0,#2f4a6a 55%,#9aa3a8)}
.card-badge{position:absolute;left:50%;top:-22px;transform:translateX(-50%);width:46px;height:46px;border-radius:50%;background:var(--red);border:3px solid #fff;display:flex;align-items:center;justify-content:center}
.card-label{position:absolute;left:13px;right:13px;bottom:-18px;height:44px;background:linear-gradient(90deg,var(--red),var(--red-soft));color:#fff;font-size:16px;font-weight:500;display:flex;align-items:center;justify-content:center;border-radius:3px}

/* quote */
.quote{height:94px;background:linear-gradient(90deg,#e8373e,var(--red-soft));display:flex;align-items:center;padding-left:51px;gap:0}
.quote-icon{width:36px}
.quote-label{color:#fff;font-size:12.5px;margin:0 29px 0 18px;white-space:nowrap}
.field{height:33px;background:#fff;border-radius:3px;font-size:12px;color:#aaa;padding:9px 14px;width:253px;margin-right:19px}
.send{height:33px;width:80px;background:#fff;border-radius:3px;color:var(--ink);font-size:12.5px;font-weight:700;display:flex;align-items:center;justify-content:center}

/* why */
.why{height:250px;padding-top:24px}
.why .dotted{margin-top:12px}
.steps{width:1097px;margin:34px auto 0;position:relative;height:130px}
.steps-line{position:absolute;top:47px;left:180px;right:180px;border-top:1.5px solid #d87a7d}
.step{position:absolute;top:0;width:220px;text-align:center}
.step-circle{width:94px;height:94px;border-radius:50%;margin:0 auto;background:linear-gradient(135deg,#e8262d,#f17579);display:flex;align-items:center;justify-content:center;box-shadow:0 0 0 5px #fde8e8;position:relative;z-index:1}
.step.feature .step-circle{box-shadow:0 0 0 3px #fff,0 0 0 5px var(--red)}
.step-label{margin-top:27px;font-size:17px;font-weight:500;color:var(--ink)}
.step.feature .step-label{color:var(--red)}

/* work */
.work-head{height:82px;background:var(--grey-bg);padding-top:18px}
.work-head .dotted{margin-top:12px}
.work-grid{display:flex}
.work-item{width:240px}
.work-logo{height:65px;display:flex;align-items:center;justify-content:center;font-size:26px;font-weight:700;background:#fff}
.work-item:nth-child(2) .work-logo{background:#f6e600}
.work-photo{height:122px;position:relative}
.zoom{position:absolute;right:8px;bottom:8px}

/* testimonials */
.testimonials{height:241px;padding-top:52px}
.testimonials .dotted{margin-top:12px}
.quotes{width:1097px;margin:30px auto 0;display:flex;position:relative}
.quote-block{width:50%;display:flex;gap:20px;align-items:flex-start}
.quote-block p{font-size:12.5px;font-style:italic;line-height:20px;color:#555}
.quote-block .who{font-style:normal;font-size:12.5px;color:var(--ink);margin-top:8px}
.left{justify-content:flex-end;padding-right:30px;text-align:right}
.right{padding-left:30px}
.avatar{width:76px;height:76px;border-radius:50%;flex:none;background:linear-gradient(135deg,#d9c3b1,#8a6a55)}
.quotes-divider{position:absolute;left:548px;top:0;height:76px;border-left:2px dotted var(--line)}

/* like bar */
.like-bar{height:65px;background:var(--grey-bg);position:relative}
.like-bar-line{position:absolute;top:32px;left:68px;right:68px;border-top:1px solid #ddd}
.like-box{position:absolute;left:374px;top:12px;width:450px;height:46px;background:#fff;border:1px solid #e3e3e3;border-radius:23px;display:flex;align-items:center}
.like-thumb{width:60px;height:100%;border-right:1px solid #e3e3e3;display:flex;align-items:center;justify-content:center}
.like-btn{margin-left:60px;background:#4a6fb5;color:#fff;font-size:10px;font-weight:700;padding:3px 6px;border-radius:2px}
.like-text{font-size:10px;color:#333;margin-left:8px}

/* footer */
.site-footer{height:401px;background:linear-gradient(90deg,#e8353c,var(--red-soft));color:#fff;position:relative}
.col-title{font-size:18px;font-weight:500}
.contact{position:absolute;left:51px;top:28px;width:260px;font-size:12.5px;line-height:20px}
.contact p{margin-top:14px}
.socials{display:flex;gap:14px;margin-top:16px}
.socials span{width:11px;height:11px;border-radius:50%;background:#fff}
.hq{position:absolute;left:332px;top:28px;width:535px;text-align:center}
.map{margin-top:16px;height:226px;background:linear-gradient(135deg,#f1ece2,#e7e3da 50%,#a9c6e8)}
.about{position:absolute;left:894px;top:28px;width:254px;font-size:12.5px;line-height:20px}
.about p{margin-top:14px}
.footer-rule{position:absolute;left:51px;right:51px;top:342px;border-top:1px solid rgba(255,255,255,.6)}
.footer-bottom{position:absolute;left:51px;right:51px;top:362px;display:flex;justify-content:space-between;align-items:center;font-size:11.5px;font-weight:700}
.footer-brand{font-size:22px;font-weight:700}
</style>
</head>
<body>

<header class="site-header">
  <div class="brand"><span class="brand-mark"></span><span class="brand-name">Varno</span></div>
  <nav class="main-nav"><span>Our Company</span><span>Services</span><span>Our Work</span><span>Contact</span></nav>
  <div class="chat">Chat 💬</div>
  <div class="call-btn">Call: 13 6419</div>
</header>

<section class="hero" role="img" aria-label="Modern two-storey house lit up at dusk">
  <h1 class="hero-title">DO YOU<br><strong>NEED</strong><br>A<br>ELECTRICIAN</h1>
</section>

<section class="welcome">
  <h2 class="section-title">Welcome to <span>Varno Electrical</span></h2>
  <div class="dotted"></div>
  <p>Varno Electrical was formed to be an expert Electricity Contracting Company providing services to all Residential and Commercial Customers. With over 10 years of experience, Varno Electrical has developed a highly-experienced team of professionals that ensure all our customer expectations are met.</p>
</section>

<section class="services">
  <div class="tabs"><span class="tab active">Residential</span><span class="tab">Commercial</span><span class="tab">Property Management</span></div>
  <div class="dotted"></div>
  <div class="cards">
    <div class="card">
      <div class="card-photo" role="img" aria-label="Electrician testing a switchboard with a multimeter"></div>
      <div class="card-badge"><svg width="20" height="20" viewBox="0 0 20 20"><path d="M6 14l8-8M4 12l4 4M12 4l4 4" stroke="#fff" stroke-width="2" fill="none" stroke-linecap="round"/></svg></div>
      <div class="card-label">Electrical</div>
    </div>
    <div class="card">
      <div class="card-photo" role="img" aria-label="Warehouse interior with LED high-bay lighting"></div>
      <div class="card-badge"><svg width="20" height="20" viewBox="0 0 20 20"><circle cx="10" cy="8" r="5" stroke="#fff" stroke-width="1.8" fill="none"/><path d="M8 15h4M8.5 18h3" stroke="#fff" stroke-width="1.8"/></svg></div>
      <div class="card-label">Led Lighting</div>
    </div>
    <div class="card">
      <div class="card-photo" role="img" aria-label="Workers installing rooftop solar panels"></div>
      <div class="card-badge"><svg width="20" height="20" viewBox="0 0 20 20"><path d="M3 15l3-10h8l3 10z M7.5 5l-1 10 M12.5 5l1 10 M4.5 10h11" stroke="#fff" stroke-width="1.5" fill="none"/></svg></div>
      <div class="card-label">Solar Power</div>
    </div>
  </div>
</section>

<section class="quote">
  <svg class="quote-icon" width="36" height="26" viewBox="0 0 36 26"><ellipse cx="14" cy="10" rx="12" ry="8" stroke="#fff" stroke-width="2" fill="none"/><path d="M24 8c6 1 10 4 10 8 0 2-1 4-3 5l1 4-5-3c-3 0-6-1-8-3" stroke="#fff" stroke-width="2" fill="none"/></svg>
  <span class="quote-label">Request a Quote</span>
  <div class="field">Full Name *</div>
  <div class="field">Phone Number *</div>
  <div class="field">Your Email *</div>
  <div class="send">SEND</div>
</section>

<section class="why">
  <h2 class="section-title">Why <span>Choose Us</span></h2>
  <div class="dotted"></div>
  <div class="steps">
    <div class="steps-line"></div>
    <div class="step" style="left:-22px">
      <div class="step-circle"><svg width="40" height="40" viewBox="0 0 40 40"><circle cx="20" cy="20" r="12" stroke="#fff" stroke-width="3" fill="none" stroke-dasharray="5 3"/><circle cx="20" cy="20" r="5" fill="#fff"/></svg></div>
      <div class="step-label">Professional Service</div>
    </div>
    <div class="step" style="left:249px">
      <div class="step-circle"><svg width="40" height="40" viewBox="0 0 40 40"><path d="M8 21l8 8 16-18" stroke="#fff" stroke-width="5" fill="none" stroke-linecap="round" stroke-linejoin="round"/></svg></div>
      <div class="step-label">5 Year Guarantee</div>
    </div>
    <div class="step feature" style="left:529px">
      <div class="step-circle"><svg width="40" height="40" viewBox="0 0 40 40"><circle cx="20" cy="17" r="6" fill="#fff"/><path d="M20 4v4M20 26v4M7 17h4M29 17h4M11 8l3 3M29 8l-3 3M10 32c4-4 16-4 20 0" stroke="#fff" stroke-width="2.5" fill="none" stroke-linecap="round"/></svg></div>
      <div class="step-label">Environmentally friendly</div>
    </div>
    <div class="step" style="left:798px">
      <div class="step-circle"><svg width="40" height="40" viewBox="0 0 40 40"><rect x="7" y="11" width="26" height="19" rx="3" stroke="#fff" stroke-width="2.5" fill="none"/><path d="M24 18h9v6h-9z" stroke="#fff" stroke-width="2.5" fill="none"/></svg></div>
      <div class="step-label">Value for Money</div>
    </div>
  </div>
</section>

<section class="work">
  <div class="work-head">
    <h2 class="section-title">Our <span>Work</span></h2>
    <div class="dotted"></div>
  </div>
  <div class="work-grid">
    <div class="work-item"><div class="work-logo" style="color:#d8232a">Lumaville</div><div class="work-photo" role="img" aria-label="Retail store interior" style="background:linear-gradient(180deg,#b9bcc5,#6c6f86)"><svg class="zoom" width="28" height="28" viewBox="0 0 28 28"><circle cx="12" cy="12" r="8" stroke="#fff" stroke-width="2.5" fill="none"/><path d="M18 18l7 7M9 12h6M12 9v6" stroke="#fff" stroke-width="2.5"/></svg></div></div>
    <div class="work-item"><div class="work-logo" style="color:#1d1d1d">Outback Depot</div><div class="work-photo" role="img" aria-label="Warehouse with lit shelving" style="background:linear-gradient(180deg,#8e8a80,#4f4a42)"><svg class="zoom" width="28" height="28" viewBox="0 0 28 28"><circle cx="12" cy="12" r="8" stroke="#fff" stroke-width="2.5" fill="none"/><path d="M18 18l7 7M9 12h6M12 9v6" stroke="#fff" stroke-width="2.5"/></svg></div></div>
    <div class="work-item"><div class="work-logo" style="color:#1d1d1d">Stonewell</div><div class="work-photo" role="img" aria-label="Industrial building exterior" style="background:linear-gradient(180deg,#d9dde4,#b03038 70%,#555)"><svg class="zoom" width="28" height="28" viewBox="0 0 28 28"><circle cx="12" cy="12" r="8" stroke="#fff" stroke-width="2.5" fill="none"/><path d="M18 18l7 7M9 12h6M12 9v6" stroke="#fff" stroke-width="2.5"/></svg></div></div>
    <div class="work-item"><div class="work-logo" style="color:#555">Marrow Signs</div><div class="work-photo" role="img" aria-label="Factory floor with overhead lighting" style="background:linear-gradient(180deg,#a7a7a3,#5b5a55)"><svg class="zoom" width="28" height="28" viewBox="0 0 28 28"><circle cx="12" cy="12" r="8" stroke="#fff" stroke-width="2.5" fill="none"/><path d="M18 18l7 7M9 12h6M12 9v6" stroke="#fff" stroke-width="2.5"/></svg></div></div>
    <div class="work-item"><div class="work-logo" style="color:#1f6fb5">Feralta Steel</div><div class="work-photo" role="img" aria-label="Steel warehouse interior" style="background:linear-gradient(180deg,#9fa6ad,#4d5760)"><svg class="zoom" width="28" height="28" viewBox="0 0 28 28"><circle cx="12" cy="12" r="8" stroke="#fff" stroke-width="2.5" fill="none"/><path d="M18 18l7 7M9 12h6M12 9v6" stroke="#fff" stroke-width="2.5"/></svg></div></div>
  </div>
</section>

<section class="testimonials">
  <h2 class="section-title">What <span>People Say</span></h2>
  <div class="dotted"></div>
  <div class="quotes">
    <div class="quote-block left">
      <div><p>Duis aute irure dolor in reprehenderit in voluptate velit esse cillum dolore eu fugiat nulla pariatur. Excepteur sint occaecat cupidatat non proident, sunt in culpa qui officia deserunt mollit.</p><p class="who">Mark Ellison, Operations Manager</p></div>
      <div class="avatar" role="img" aria-label="Portrait of client"></div>
    </div>
    <div class="quotes-divider"></div>
    <div class="quote-block right">
      <div class="avatar" role="img" aria-label="Portrait of client"></div>
      <div><p>Provident, similique sunt in culpa qui officia deserunt mollitia animi, id est laborum et dolorum fuga. Et harum quidem rerum facilis est et expedita distinctio. Nam libero tempore, cum soluta nobis.</p><p class="who">Nora Castell, Creative Designer</p></div>
    </div>
  </div>
</section>

<div class="like-bar">
  <div class="like-bar-line"></div>
  <div class="like-box">
    <div class="like-thumb"><svg width="18" height="18" viewBox="0 0 18 18"><path d="M2 8h3v8H2zM6 8l4-6c1 0 2 1 2 2l-1 3h4c1 0 2 1 1.5 2l-2 6H6z" fill="none" stroke="#bbb" stroke-width="1.3"/></svg></div>
    <span class="like-btn">✔ Like</span><span class="like-text">You and 4k others like this.</span>
  </div>
</div>

<footer class="site-footer">
  <div class="contact">
    <h3 class="col-title">Contact Us</h3>
    <p>Please feel free to contact us for any issue. Our staff is available to you from 9AM until 5PM on weekdays.</p>
    <p><strong>Phone:</strong> 13 64 19</p>
    <p><strong>Office:</strong> 8/214 Halden Rd Glen Ashby</p>
    <p><strong>Email:</strong> service@varnoelectrical-example.com.au</p>
    <div class="socials"><span></span><span></span><span></span><span></span><span></span></div>
  </div>
  <div class="hq">
    <h3 class="col-title">Headquarters</h3>
    <div class="map" role="img" aria-label="Street map showing office location"></div>
  </div>
  <div class="about">
    <h3 class="col-title">About Team</h3>
    <p>Enim congue blandit. Lorem ipsum dolor sit amet, consectetur adipiscing elit. Quisque consectetur interdum finibus. Vestibulum ante ipsum primis in faucibus orci. luctus et ultrices posuere.</p>
    <p>Cubilia cras blandit finibus ipsum, id porttitor arcu volutpat a. Integer iaculis erat nec justo malesuada faucibus vel tempus sapien. Vivamus aliquam euismod tristique.</p>
  </div>
  <div class="footer-rule"></div>
  <div class="footer-bottom">
    <span>Copyright © Varno Electrical</span>
    <span class="footer-brand">Varno</span>
    <span>All rights reserved</span>
  </div>
</footer>

</body>
</html>
```